Dancing Emoji Lady but make it silhouette

We need a main image for the front of a hard wine seltzer. The best emoji that would describe this brand is the dancing lady in red dress emoji. We want to re-create the essence of this emoji in a silhouette (like an outline) so it's our own design, but it captures the fun and flirtatiousness of that emoji. We have three flavors - peach (peach color), fruit punch (red/purple color), and citrus (orange color) - so the only color should be the outline of her swooshing dress.

I'm attaching an image of the emoji I wish to emulate, and then some examples of what I mean by "silhouette" - I know the attached examples are not of a woman dancing, but it's the line/style that I want to emulate here to make a silhouette of the dancer emoji.

```html
<!DOCTYPE html>
<html lang="en">
<head>
<meta charset="utf-8">
<title>Lumera Peach Bellini — Can Label</title>
<link rel="stylesheet" href="https://fonts.googleapis.com/css2?family=Fraunces:opsz,wght@9..144,600;9..144,700&family=Oswald:wght@400;500&display=swap">
<style>
  :root {
    --stage: #ebebeb;
    --peach: #f8a590;
    --brown: #6e1c08;
    --dress-red: #c8231c;
    --cream: #ffffff;
  }
  * { box-sizing: border-box; margin: 0; padding: 0; }
  html, body {
    width: 1200px;
    height: 738px;
    overflow: hidden;
    background: var(--stage);
  }
  .label {
    position: absolute;
    left: 406px;
    top: 57px;
    width: 388px;
    height: 624px;
    background: var(--peach);
  }
  .label > * {
    position: absolute;
    left: 0;
    right: 0;
    text-align: center;
  }
  .brand-dot {
    left: 187px;
    right: auto;
    top: 50px;
    width: 14px;
    height: 14px;
    border-radius: 50%;
    background: var(--cream);
  }
  .brand-name {
    top: 72px;
    font-family: "Fraunces", Georgia, serif;
    font-weight: 700;
    font-size: 64px;
    line-height: 1;
    color: var(--brown);
    letter-spacing: -0.5px;
  }
  .dancer-art {
    left: 67px;
    right: auto;
    top: 158px;
    width: 209px;
    height: 248px;
    border-radius: 40% 30% 45% 35%;
    background: radial-gradient(ellipse at 60% 60%, rgba(200,35,28,0.55), rgba(200,35,28,0.15) 60%, rgba(248,165,144,0) 75%);
  }
  .flavor-name {
    top: 428px;
    font-family: "Oswald", "Arial Narrow", sans-serif;
    font-weight: 400;
    font-size: 36px;
    line-height: 1;
    color: var(--cream);
    letter-spacing: 0.5px;
  }
  .product-type {
    top: 468px;
    font-family: "Fraunces", Georgia, serif;
    font-weight: 600;
    font-size: 16px;
    color: var(--brown);
  }
  .claims {
    top: 496px;
    left: 109px;
    right: 110px;
    height: 36px;
    display: flex;
    align-items: center;
    justify-content: space-between;
  }
  .claim-badge {
    width: 36px;
    height: 36px;
    border: 1.2px solid var(--brown);
    border-radius: 50%;
    display: flex;
    align-items: center;
    justify-content: center;
    font-family: "Oswald", "Arial Narrow", sans-serif;
    font-weight: 500;
    font-size: 6px;
    line-height: 1.15;
    color: var(--brown);
    text-align: center;
  }
  .claim-main {
    font-family: "Oswald", "Arial Narrow", sans-serif;
    font-weight: 500;
    font-size: 10px;
    line-height: 1.5;
    color: var(--brown);
    text-align: center;
  }
  .volume {
    top: 543px;
    font-family: "Oswald", "Arial Narrow", sans-serif;
    font-weight: 500;
    font-size: 10px;
    color: var(--brown);
    letter-spacing: 0.3px;
  }
</style>
</head>
<body>
  <main class="label">
    <div class="brand-dot"></div>
    <h1 class="brand-name">lumera</h1>
    <div class="dancer-art" role="img" aria-label="Line illustration of a woman dancing in a swirling red dress, raising a glass of wine"></div>
    <h2 class="flavor-name">PEACH BELLINI</h2>
    <p class="product-type">Hard Wine Seltzer</p>
    <div class="claims">
      <div class="claim-badge">ONLY 120<br>CALORIES</div>
      <div class="claim-main">MADE WITH<br>ORGANIC GRAPES</div>
      <div class="claim-badge">NO ADDED<br>SUGAR</div>
    </div>
    <p class="volume">6% ABV &nbsp;|&nbsp; 250 mL</p>
  </main>
</body>
</html>
```